Professional consulting firm needing a Word document template

I need a Word document template that can be used flexibly for a flyer or brochure of 1 to 3 pages in length. The first page should be designed in a way that it can stand alone as a one-page flyer without a formal cover page. I have attached sample text as a Word document that could be used as the basis for the first 1-2 pages, however I do need three page layouts designed to give flexibility to use as a 3 page booklet. I have attached our brand guidelines, logo, and some stock images that I have previously purchased (they may not all be useful but it gives some options). <br/>The Word document needs to be set up in away that it can easily be edited to accommodate updates to the text, and some variation in the quantity of text on each page. Each page should be able to accommodate a mixture of paragraph text, bullet points, small boxes to call out highlights, one or more images, and some white space to avoid clutter. It should look professional yet engaging and modern.

Font styles to use
Sans Serif

Requirements
Must have
• Must be an editable Microsoft Word document, using the text provided. Must be a layout suitable to use as 1 page, up to 3 pages. Must comply with brand guidelines.

```html
<!DOCTYPE html>
<html lang="en">
<head>
<meta charset="utf-8">
<title>Train Driver Competency Indicator Development Project – Brochure</title>
<link rel="stylesheet" href="https://fonts.googleapis.com/css2?family=Open+Sans:wght@400;600;700&display=swap">
<style>
:root{
  --stage:#d9d9d9;
  --navy:#14263a;
  --cyan:#29b5e3;
  --cyan-light:#7fd3ef;
  --ink:#5a5f66;
  --white:#ffffff;
}
*{margin:0;padding:0;box-sizing:border-box}
html,body{width:1200px;height:509px;overflow:hidden;background:var(--stage);font-family:"Open Sans",Arial,sans-serif;color:var(--ink)}
.page{position:absolute;top:27px;width:325px;height:457px;background:var(--white);box-shadow:1px 2px 4px rgba(0,0,0,.35);overflow:hidden}
.page-one{left:85px}
.page-two{left:440px}
.page-three{left:806px}
.abs{position:absolute}
.shape{position:absolute;left:0;top:0}
.brand{left:14px;top:18px;font-size:17px;font-weight:700;letter-spacing:1px;color:var(--navy)}
.hero-title{left:13px;top:78px;width:150px;color:var(--white);font-size:9.5px;font-weight:700;line-height:11px}
.hero-intro{left:13px;top:122px;width:170px;color:var(--white);font-size:5.3px;line-height:8px}
.body{font-size:6px;line-height:8.6px;color:var(--ink)}
.bullets{list-style:none;font-size:6.2px;line-height:11.2px}
.bullets li{position:relative;padding-left:10px}
.bullets li::before{content:"";position:absolute;left:0;top:3px;width:5px;height:5px;border-radius:50%;background:var(--cyan)}
.band{position:absolute;left:0;width:325px;background:var(--cyan);color:var(--white)}
.band-title{text-align:center;font-weight:700;font-size:7.6px;padding-top:5px}
.band-text{text-align:center;font-size:5.9px;line-height:8.6px;padding:6px 12px 0}
.footer{position:absolute;left:0;bottom:0;width:325px;height:27px}
.footer a{position:absolute;top:10px;font-size:6.2px;text-decoration:underline}
.footer .mail{left:38px;color:var(--white)}
.footer .web{left:224px;color:var(--navy)}
.photo{position:absolute;left:0;top:0}
.panel-title{color:var(--white);font-size:8.8px;font-weight:700;line-height:15px}
.panel-text{color:var(--white);font-size:5.3px;line-height:7.9px;text-align:justify}
.section-title{color:var(--cyan);font-weight:700;font-size:7.5px}
.activity{position:absolute;width:145px}
.activity h3{font-size:5.3px;color:var(--white);text-decoration:underline;font-weight:700;margin-left:25px;line-height:6.5px}
.activity p{font-size:4.7px;line-height:6.2px;color:var(--white);margin:4px 0 0 25px;text-align:justify}
.activity svg{position:absolute;left:1px;top:0}
.divider-v{position:absolute;left:162px;top:8px;width:.6px;height:110px;background:var(--white)}
.divider-h{position:absolute;left:15px;top:61px;width:296px;height:.6px;background:var(--white)}
.highlight{position:absolute;left:12px;width:300px;height:24px}
.highlight .icon{position:absolute;left:0;top:0;width:24px;height:24px}
.highlight p{position:absolute;left:50px;top:3px;width:250px;color:var(--white);font-size:5.9px;line-height:8.8px}
.two-col{columns:2;column-gap:12px;text-align:justify;color:#777}
</style>
</head>
<body>

<!-- Page one -->
<section class="page page-one">
  <svg class="shape" width="325" height="457" viewBox="0 0 325 457">
    <rect x="0" y="55" width="325" height="111" fill="var(--navy)"/>
  </svg>
  <svg class="photo" width="325" height="166" viewBox="0 0 325 166" role="img" aria-label="Photo of a high-speed train passing a platform in streaks of light">
    <defs>
      <linearGradient id="speed" x1="0" y1="0" x2="1" y2="1">
        <stop offset="0" stop-color="#1c6b8c"/>
        <stop offset=".45" stop-color="#4fc0c6"/>
        <stop offset=".7" stop-color="#9fe0b0"/>
        <stop offset="1" stop-color="#d9f3f5"/>
      </linearGradient>
    </defs>
    <polygon points="178,0 325,0 325,166 200,166" fill="url(#speed)"/>
  </svg>
  <div class="abs brand">NORVANTA</div>
  <h1 class="abs hero-title">TRAIN DRIVER<br>COMPETENCY INDICATOR<br>DEVELOPMENT PROJECT</h1>
  <p class="abs hero-intro">We are commencing an applied research project to develop and test a framework of underlying core competencies for train driver performance.</p>

  <p class="abs body" style="left:13px;top:180px;width:300px">The objective of the project is to identify observable indicators that describe effective performance in the following types of underlying competencies:</p>
  <ul class="abs bullets" style="left:23px;top:204px">
    <li>Application of Procedures</li>
    <li>Communication</li>
    <li>Operation of Tools / Equipment</li>
    <li>Problem Solving and Decision Making</li>
    <li>Route Knowledge</li>
    <li>Self Management</li>
  </ul>
  <ul class="abs bullets" style="left:185px;top:204px">
    <li>Situation Awareness</li>
    <li>System Knowledge</li>
    <li>Teamwork and Leadership</li>
    <li>Train Handling</li>
    <li>Workload Management</li>
  </ul>

  <div class="band" style="top:288px;height:61px">
    <h2 class="band-title">Underlying competencies:</h2>
    <p class="band-text">The underpinning knowledge and skills required by a train driver, to perform a range of different tasks effectively. Underlying competencies include both ‘technical’ and ‘non-technical’ skills. They are not specific to one driving task, but help build resilient performance across all tasks, conditions or situations that a driver may encounter.</p>
  </div>

  <p class="abs body" style="left:14px;top:370px;width:298px;color:#777">In contrast to other performance marker systems, the current project aims to include both ‘technical’ and ‘non-technical’ skills in an integrated framework, with substantial input from drivers across the industry, both in passenger and freight operations. The aim is to develop a framework that uses a language that describes performance in a way that is relatable to drivers, trainers, and assessors.</p>

  <footer class="footer">
    <svg class="shape" width="325" height="27" viewBox="0 0 325 27">
      <rect width="325" height="27" fill="var(--cyan)"/>
      <polygon points="0,0 160,0 177,27 0,27" fill="var(--navy)"/>
    </svg>
    <a class="mail">contact@norvanta.com.au</a>
    <a class="web" style="left:225px;top:8px">www.norvanta.com.au</a>
  </footer>
</section>

<!-- Page two -->
<section class="page page-two">
  <svg class="shape" width="325" height="180" viewBox="0 0 325 180">
    <polygon points="0,0 325,0 325,112 0,160" fill="var(--navy)"/>
    <polygon points="0,160 325,112 325,121 0,174" fill="var(--cyan)"/>
  </svg>
  <svg class="photo" width="325" height="140" viewBox="0 0 325 140" role="img" aria-label="Photo of a city rail line running between tall buildings at dusk">
    <defs>
      <linearGradient id="city" x1="0" y1="0" x2="0" y2="1">
        <stop offset="0" stop-color="#3a4b5c"/>
        <stop offset=".5" stop-color="#9a8670"/>
        <stop offset="1" stop-color="#cdb89a"/>
      </linearGradient>
    </defs>
    <polygon points="159,0 325,0 325,112 159,136.5" fill="url(#city)"/>
  </svg>
  <h2 class="abs panel-title" style="left:25px;top:20px">What are the benefits for<br>participating organisations?</h2>
  <p class="abs panel-text" style="left:24px;top:60px;width:123px">All participating rail organisations will receive a copy of the performance indicator framework, which they are free to use or adapt for application within their own operation. A summary report will also be provided, outlining the methodology and aggregated results of the data collection activities. All results will be presented in a de-identified way, to ensure the anonymity of participating organisations and individuals.</p>

  <h2 class="abs section-title" style="left:16px;top:185px">What is involved?</h2>
  <p class="abs body" style="left:16px;top:200px;width:298px">Participating organisations will be invited to provide in-kind support for the following activities during the period April – June 2020:</p>

  <div class="band" style="top:228px;height:123px">
    <div class="divider-v"></div>
    <div class="divider-h"></div>
    <div class="activity" style="left:15px;top:8px">
      <svg width="20" height="16" viewBox="0 0 20 16"><path d="M1 1h12v8H6l-3 3V9H1z" fill="var(--navy)"/><path d="M8 6h11v7h-2v3l-3-3H8z" fill="none" stroke="var(--navy)" stroke-width="1.4"/></svg>
      <h3>Interviews with volunteer Driver participants:</h3>
      <p>individual discussions with our researchers about drivers’ previous experiences, to gather information about expert driving strategies and positive techniques used in normal and abnormal operations</p>
    </div>
    <div class="activity" style="left:166px;top:8px">
      <svg width="16" height="20" viewBox="0 0 16 20"><rect x="4" y="1" width="8" height="3" fill="var(--navy)"/><circle cx="8" cy="7.5" r="3" fill="var(--navy)"/><path d="M2 19c0-5 2.5-8 6-8s6 3 6 8z" fill="var(--navy)"/></svg>
      <h3>Initial workshop:</h3>
      <p>a facilitated group workshop to understand the links between underlying competencies and driving tasks, and to understand Drivers’ perceptions of what each underlying competency looks like in practice.</p>
    </div>
    <div class="activity" style="left:15px;top:67px">
      <svg width="16" height="20" viewBox="0 0 16 20"><rect x="1" y="1" width="14" height="14" rx="3" fill="var(--navy)"/><rect x="3" y="3.5" width="10" height="5" fill="var(--cyan)"/><circle cx="4.5" cy="12" r="1.2" fill="var(--cyan)"/><circle cx="11.5" cy="12" r="1.2" fill="var(--cyan)"/><path d="M3 19l2-4M13 19l-2-4" stroke="var(--navy)" stroke-width="1.4"/></svg>
      <h3>Driver Training Survey:</h3>
      <p>a voluntary survey will be distributed, requesting Driver Trainers’ and Assessors’ views on the importance of underlying competencies in driving performance, and further data about expert driving strategies and techniques.</p>
    </div>
    <div class="activity" style="left:166px;top:67px">
      <svg width="18" height="18" viewBox="0 0 18 18"><circle cx="9" cy="9" r="8" fill="var(--navy)"/><circle cx="6" cy="7" r="2.2" fill="var(--cyan)"/><circle cx="12" cy="11" r="2.2" fill="var(--cyan)"/></svg>
      <h3>Follow-up workshop:</h3>
      <p>a facilitated group workshop to test and refine the performance indicators. Where possible, indicators will be tested through participants providing ratings of a video sample of actual performance, to determine whether multiple rates can distinguish between competency categories.</p>
    </div>
  </div>

  <p class="abs body" style="left:16px;top:367px;width:300px;color:#777">It is anticipated that workshops will be run in Brisbane, Sydney and Melbourne. We would appreciate support from participating organisations in providing a workshop venue where possible. Apart from the in-kind support of providing access to personnel and a meeting room, there is no cost associated with participation in the project.</p>
  <p class="abs body" style="left:16px;top:406px;width:300px;color:#777">We look forward to hearing from organisations interested in being part of this landmark project.</p>

  <footer class="footer">
    <svg class="shape" width="325" height="27" viewBox="0 0 325 27">
      <rect width="325" height="27" fill="var(--cyan)"/>
      <polygon points="0,0 160,0 177,27 0,27" fill="var(--navy)"/>
    </svg>
    <a class="mail" style="left:35px">contact@norvanta.com.au</a>
    <a class="web" style="left:223px;top:8px">www.norvanta.com.au</a>
  </footer>
</section>

<!-- Page three -->
<section class="page page-three">
  <svg class="shape" width="325" height="152" viewBox="0 0 325 152">
    <rect width="325" height="152" fill="var(--navy)"/>
    <polygon points="146,0 155,0 210,152 201,152" fill="var(--cyan-light)"/>
  </svg>
  <svg class="photo" width="325" height="152" viewBox="0 0 325 152" role="img" aria-label="Photo of a train cab control desk with a track view through the windscreen">
    <defs>
      <linearGradient id="cab" x1="0" y1="0" x2="1" y2="1">
        <stop offset="0" stop-color="#8c7a8e"/>
        <stop offset=".5" stop-color="#4b5f7a"/>
        <stop offset="1" stop-color="#1d2c44"/>
      </linearGradient>
    </defs>
    <polygon points="155,0 325,0 325,152 210,152" fill="url(#cab)"/>
  </svg>
  <h2 class="abs panel-title" style="left:15px;top:22px;line-height:17.5px">Train Driver Performance<br>from Train Monitoring</h2>
  <p class="abs panel-text" style="left:15px;top:76px;width:136px">In contrast to other performance marker systems, the current project aims to include both ‘technical’ and ‘non-technical’ skills in an integrated framework, with substantial input from drivers across the industry, both in passenger and freight operations.</p>

  <p class="abs" style="left:16px;top:176px;color:var(--cyan);font-size:6.4px">Lorem Ipsum. Proin gravida</p>
  <p class="abs body" style="left:16px;top:190px;width:298px">In contrast to other performance marker systems, the current project aims to include both ‘technical’ and ‘non-technical’ skills in an integrated framework, with substantial input from drivers across the industry, both in passenger and freight operations.</p>

  <div class="band" style="top:232px;height:122px">
    <div class="highlight" style="top:7px">
      <svg class="icon" viewBox="0 0 24 24"><circle cx="12" cy="12" r="11" fill="var(--navy)" stroke="var(--white)" stroke-width=".8"/><rect x="6" y="11" width="12" height="2" fill="var(--white)"/><circle cx="12" cy="8" r="2" fill="var(--white)"/><rect x="10.5" y="13" width="3" height="5" fill="var(--white)"/></svg>
      <p>Lorem Ipsum. Proin gravida nibh vel velit auctor aliquet. Aenean sollicitudin, lorem quis bibendum auctor Aenean sollicitudin, lorem quis bibendum auctor</p>
    </div>
    <div class="highlight" style="top:48px">
      <svg class="icon" viewBox="0 0 24 24"><circle cx="12" cy="12" r="11" fill="var(--navy)" stroke="var(--white)" stroke-width=".8"/><rect x="8" y="6" width="8" height="11" fill="none" stroke="var(--white)" stroke-width="1.2"/><path d="M10 9h4M10 11.5h4M10 14h3" stroke="var(--white)" stroke-width=".9"/></svg>
      <p>Lorem Ipsum. Proin gravida nibh vel velit auctor aliquet. Aenean sollicitudin, lorem quis bibendum auctor Aenean sollicitudin, lorem quis bibendum auctor Aenean sollicitudin, lorem quis bibendum auctor</p>
    </div>
    <div class="highlight" style="top:90px">
      <svg class="icon" viewBox="0 0 24 24"><circle cx="12" cy="12" r="11" fill="var(--navy)" stroke="var(--white)" stroke-width=".8"/><circle cx="12" cy="8" r="2.2" fill="var(--white)"/><rect x="11" y="10" width="2" height="5" fill="var(--white)"/><rect x="7" y="15" width="10" height="2.5" fill="var(--white)"/></svg>
      <p>Lorem Ipsum. Proin gravida nibh vel velit auctor aliquet. Aenean sollicitudin, lorem quis bibendum auctor Aenean sollicitudin, lorem quis bibendum auctor</p>
    </div>
  </div>

  <div class="abs body two-col" style="left:17px;top:370px;width:297px;column-gap:14px">
    <p>With substantial input from drivers across the industry, both in passenger and freight operations. The aim is to develop a framework that uses a language that describes performance in a way that is relatable to drivers, trainers, and assessors.</p>
    <p>With substantial input from drivers across the industry, both in passenger and freight operations. The aim is to develop a framework that uses a language that describes performance in a way that is relatable to drivers, trainers, and assessors.</p>
  </div>

  <footer class="footer">
    <svg class="shape" width="325" height="27" viewBox="0 0 325 27">
      <rect width="325" height="27" fill="var(--cyan)"/>
      <polygon points="0,0 163,0 180,27 0,27" fill="var(--navy)"/>
    </svg>
    <a class="mail" style="left:32px">contact@norvanta.com.au</a>
    <a class="web" style="left:219px;top:8px">www.norvanta.com.au</a>
  </footer>
</section>

</body>
</html>
```